Bright Meadow Kitchen Business Cards

We need Business cards development for our expanding business. Our Company BrightMeadowKitchen promotes grain free living through products, services and healthy living concepts. Our Products are:
Non-Grain
Non- GMO
Non- Soy
Gluten-Free
Updates

Project Deadline Extended
Reason: We will need to extend the deadline on our Business Card contest. Thanks, BMK

Industry/Entity Type

Business

```html
<!DOCTYPE html>
<html lang="en">
<head>
<meta charset="utf-8">
<title>Bright Meadow Kitchen – Business Card</title>
<link rel="stylesheet" href="https://fonts.googleapis.com/css2?family=Mulish:wght@400;700&family=Alegreya+Sans+SC:wght@700&display=swap">
<style>
  :root {
    --backdrop: #e4e4e4;
    --card-white: #ffffff;
    --brand-green: #1f8a3c;
    --leaf-green: #8cc63f;
    --stripe-light: #8dc63f;
    --stripe-dark: #6fb334;
    --panel-top: #1b8a44;
    --panel-bottom: #0f6a31;
    --ink-dark: #0d4a22;
    --text-white: #ffffff;
  }
  * { margin: 0; padding: 0; box-sizing: border-box; }
  html, body {
    width: 1200px; height: 900px; overflow: hidden;
    background: var(--backdrop);
    font-family: "Mulish", "Century Gothic", sans-serif;
  }
  .canvas { position: relative; width: 1200px; height: 900px; }
  .business-card {
    position: absolute; left: 150px; top: 190px;
    width: 900px; height: 520px;
    border-radius: 42px; overflow: hidden;
    background: var(--card-white);
    box-shadow: 0 18px 40px rgba(0,0,0,0.18);
  }
  .brand {
    position: absolute; left: 66px; top: 84px;
    display: flex; align-items: center; gap: 20px;
  }
  .brand-dot {
    width: 60px; height: 60px; border-radius: 50%;
    background: var(--brand-green); flex: none;
  }
  .brand-text { position: relative; }
  .brand-name {
    font-size: 50px; font-weight: 700; color: var(--brand-green);
    letter-spacing: -0.5px; line-height: 1;
  }
  .brand-suffix {
    position: absolute; right: -30px; top: 34px;
    font-size: 13px; color: var(--brand-green);
  }
  .tagline {
    font-size: 19px; color: var(--brand-green);
    letter-spacing: 2px; margin-top: 4px; text-align: right;
  }
  .product-stripe {
    position: absolute; left: 0; top: 236px; width: 100%; height: 34px;
    background: linear-gradient(90deg, var(--stripe-dark), var(--stripe-light));
    display: flex; justify-content: space-between; align-items: center;
    padding: 0 60px;
    font-family: "Alegreya Sans SC", "Copperplate", sans-serif;
    font-weight: 700; font-size: 21px; letter-spacing: 2.5px; color: var(--ink-dark);
  }
  .contact-panel {
    position: absolute; left: 0; top: 270px; width: 100%; height: 250px;
    background: linear-gradient(180deg, var(--panel-top), var(--panel-bottom));
    padding: 22px 0 0 60px; color: var(--text-white);
  }
  .person-name { font-size: 34px; font-weight: 700; line-height: 1; }
  .person-role { font-size: 21px; color: var(--leaf-green); margin-top: 8px; line-height: 1.2; }
  .contact-list { list-style: none; margin-top: 16px; }
  .contact-list li {
    display: flex; align-items: center; gap: 16px;
    font-size: 24px; line-height: 32px;
  }
  .contact-list svg { width: 28px; height: 28px; fill: var(--leaf-green); flex: none; }
</style>
</head>
<body>
<main class="canvas">
  <section class="business-card">
    <header class="brand">
      <span class="brand-dot"></span>
      <div class="brand-text">
        <div class="brand-name">BrightMeadowKitchen</div>
        <span class="brand-suffix">LLC</span>
        <div class="tagline">Wholesome Food, Simply Made</div>
      </div>
    </header>

    <div class="product-stripe">
      <span>Non-Grain</span>
      <span>Non- GMO</span>
      <span>Non- Soy</span>
      <span>Gluten-Free</span>
    </div>

    <div class="contact-panel">
      <div class="person-name">Nora Vance</div>
      <div class="person-role">Manager</div>
      <ul class="contact-list">
        <li>
          <svg viewBox="0 0 24 24" aria-hidden="true"><path d="M6.6 10.8a15.1 15.1 0 0 0 6.6 6.6l2.2-2.2a1 1 0 0 1 1-.25 11.4 11.4 0 0 0 3.6.57 1 1 0 0 1 1 1V20a1 1 0 0 1-1 1A17 17 0 0 1 3 4a1 1 0 0 1 1-1h3.5a1 1 0 0 1 1 1c0 1.25.2 2.46.57 3.6a1 1 0 0 1-.25 1z"/></svg>
          <span>1590 214 736</span>
        </li>
        <li>
          <svg viewBox="0 0 24 24" aria-hidden="true"><path d="M12 3 2 12h3v9h5v-6h4v6h5v-9h3z"/></svg>
          <span>PO Box 40518 AL 35012</span>
        </li>
        <li>
          <svg viewBox="0 0 24 24" aria-hidden="true"><path d="M3 6h18v12H3z M3 6l9 7 9-7" fill="none" stroke="#8cc63f" stroke-width="2"/></svg>
          <span>info@brightmeadowkitchen.com</span>
        </li>
        <li>
          <svg viewBox="0 0 24 24" aria-hidden="true"><g fill="none" stroke="#8cc63f" stroke-width="1.8"><circle cx="12" cy="12" r="9"/><ellipse cx="12" cy="12" rx="4" ry="9"/><path d="M3 12h18M5 7h14M5 17h14"/></g></svg>
          <span>www.brightmeadowkitchen.com</span>
        </li>
      </ul>
    </div>
  </section>
</main>
</body>
</html>
```